Allied Health team of Physiotherapists & Occupational Therapists seek a business card design

We have our new logo, we now need our new business cards and stationary. Tidewell: Oedema & Family Clinic is seeking a generic card design to represent our whole team and individual cards for each therapist that incorporates our new logo to communicate our holistic approach that is calming, nuturing, supportive and welcoming.
Our Physiotherapists and Occupational Therapists assess, treat and provide education for people who are at risk of or who have lymphoedema. This is often as a result of treatment for cancer. We provide pre-operative and post-operative management and cancer rehabilitation in our Pilates studio. Our team also consists of Physiotherapists who have a strong interest in pelvic floor and continence management for both men and women.

Target Market(s)

Mainly women health conscious

Industry/Entity Type

Allied Health: Physiotherapy / Occupational Therapy

Contact Information for Business Card

Address: 14 Gallivant Ave Marrowby 3284 Phone: 84316570 fax: 8431 6578 Email: info@tidewellcareservices.com.au Website: tidewellcareservices.com.au Facebook address: facebook.com/TidewellOedemaAndFamilyCareClinic. Room to write appointments. Individual cards need to have name, office email and individual email and professional details

Requirements
Must have
• Logo as per uploaded documents

```html
<!DOCTYPE html>
<html lang="en">
<head>
<meta charset="utf-8">
<title>Tidewell business cards</title>
<link rel="stylesheet" href="https://fonts.googleapis.com/css2?family=Marcellus&family=Roboto:ital,wght@0,400;1,400&display=swap">
<style>
  :root {
    --backdrop: #2c2c2c;
    --peach: #df9470;
    --peach-light: #edb996;
    --sage: #8fa89c;
    --cream: #f3eeb8;
    --paper: #f2f1ef;
    --ink: #2d2d2d;
  }
  * { margin: 0; padding: 0; box-sizing: border-box; }
  html, body { width: 1200px; height: 1138px; overflow: hidden; }
  body { background: var(--backdrop); position: relative; font-family: "Roboto", sans-serif; }

  .card {
    position: absolute;
    width: 620px;
    height: 374px;
    border-radius: 16px;
    overflow: hidden;
  }
  .card-front { left: 274px; top: 186px; background: var(--peach); }
  .card-back { left: 276px; top: 608px; background: var(--paper); }

  .brand {
    position: absolute;
    display: flex;
    align-items: center;
    justify-content: center;
    text-align: center;
    border-radius: 50%;
    font-family: "Marcellus", serif;
    width: 220px; height: 220px;
    font-size: 24px; line-height: 1.3;
    padding: 28px;
  }
  .card-front .brand {
    left: 200px; top: 77px;
    border: 2px solid var(--cream);
    color: var(--cream);
  }
  .card-back .brand {
    left: 34px; top: 130px;
    border: 2px solid var(--peach);
    color: var(--peach);
  }

  .wave { position: absolute; left: 0; top: 0; width: 620px; height: 374px; }

  .person {
    position: absolute; right: 26px; top: 18px; text-align: right; color: #fff;
  }
  .person-name { font-family: "Marcellus", serif; font-size: 25px; letter-spacing: 0.5px; line-height: 31px; margin-bottom: 6px; }
  .person-role { font-size: 13.5px; line-height: 19px; }
  .person-role em { font-style: italic; }

  .contacts {
    position: absolute; right: 22px; top: 224px;
    list-style: none; color: var(--ink); font-size: 15px;
  }
  .contacts li {
    display: flex; justify-content: flex-end; align-items: center;
    height: 26px;
  }
  .contacts svg { width: 14px; height: 14px; margin-left: 6px; fill: var(--peach); }
</style>
</head>
<body>

<section class="card card-front">
  <div class="brand">Tidewell: Oedema &amp; Family Clinic</div>
</section>

<section class="card card-back">
  <svg class="wave" viewBox="0 0 620 374" aria-hidden="true">
    <path d="M0 0 H620 V158 C590 160 560 165 500 150 C300 40 180 40 0 60 Z" fill="var(--peach)"/>
    <path d="M0 60 C180 40 300 40 500 150 C560 165 590 160 620 158 V164 C585 168 555 172 495 158 C300 52 180 52 0 74 Z" fill="var(--peach-light)"/>
    <path d="M40 74 C190 60 320 70 500 166 C560 180 590 176 620 174 V181 C585 184 555 188 495 174 C320 80 190 70 40 74 Z" fill="var(--sage)"/>
  </svg>

  <div class="person">
    <p class="person-name">Maren Hollis</p>
    <p class="person-role"><em>Physiotherapist</em> &nbsp;|&nbsp; Lymphoedema &amp;</p>
    <p class="person-role">Oncology Rehabilitation</p>
    <p class="person-role">Continence &amp; Pelvic Floor</p>
  </div>

  <div class="brand">Tidewell: Oedema &amp; Family Clinic</div>

  <ul class="contacts">
    <li>8431 6570<svg viewBox="0 0 24 24"><path d="M6.6 10.8a15 15 0 006.6 6.6l2.2-2.2c.3-.3.7-.4 1-.2 1.1.4 2.3.6 3.6.6.6 0 1 .4 1 1V20c0 .6-.4 1-1 1A17 17 0 013 4c0-.6.4-1 1-1h3.5c.6 0 1 .4 1 1 0 1.3.2 2.5.6 3.6.1.3 0 .7-.2 1z"/></svg></li>
    <li>8431 6578<svg viewBox="0 0 24 24"><path d="M6.6 10.8a15 15 0 006.6 6.6l2.2-2.2c.3-.3.7-.4 1-.2 1.1.4 2.3.6 3.6.6.6 0 1 .4 1 1V20c0 .6-.4 1-1 1A17 17 0 013 4c0-.6.4-1 1-1h3.5c.6 0 1 .4 1 1 0 1.3.2 2.5.6 3.6.1.3 0 .7-.2 1z"/></svg></li>
    <li>tidewellcareservices.com.au<svg viewBox="0 0 24 24"><path d="M12 2a10 10 0 100 20 10 10 0 000-20zm6.9 6h-3a15 15 0 00-1.4-3.9A8 8 0 0118.9 8zM12 4c.8 1.2 1.5 2.5 1.9 4h-3.8c.4-1.5 1.1-2.8 1.9-4zM4.3 14a8 8 0 010-4h3.4a16 16 0 000 4zm.8 2h3a15 15 0 001.4 3.9A8 8 0 015.1 16zm3-8h-3a8 8 0 014.4-3.9A15 15 0 008.1 8zM12 20c-.8-1.2-1.5-2.5-1.9-4h3.8c-.4 1.5-1.1 2.8-1.9 4zm2.3-6H9.7a14 14 0 010-4h4.6a14 14 0 010 4zm.2 5.9a15 15 0 001.4-3.9h3a8 8 0 01-4.4 3.9zm1.8-5.9a16 16 0 000-4h3.4a8 8 0 010 4z"/></svg></li>
    <li>info@tidewellcareservices.com.au<svg viewBox="0 0 24 24"><path d="M2 5h20v14H2zm2 2v.5l8 5 8-5V7zm0 3v7h16v-7l-8 5z"/></svg></li>
    <li>14 Gallivant Ave, Marrowby 3284<svg viewBox="0 0 24 24"><path d="M12 2a7 7 0 00-7 7c0 5 7 13 7 13s7-8 7-13a7 7 0 00-7-7zm0 9.5A2.5 2.5 0 1112 6.5a2.5 2.5 0 010 5z"/></svg></li>
  </ul>
</section>

</body>
</html>
```